Dynamic Business Card for Sports Supplements Company

Hi! I'm looking for an awesome business card to match my existing sports supplement company. I have uploaded my current company logo and screenshot of the front page of my website.

I would like to have something dynamic and interesting and utilize the colors in the website - the reds and purples

The business card should be double sided and focus on a unique eye-catching design on the back and include all the relevant company info.

Most importantly, it should say somewhere: "Sign up on our website for a coupon code."

Target Market(s)

Mostly for women gym goers but it shouldn't be too feminine. It should be in keeping with the website design. It should flow and clearly be connected to it

Industry/Entity Type

Business

Contact Information for Business Card

Lorraine K. Vestal
CEO
LVestal@Quorvanexco.com
www.quorvanexco.com
555.417.3820
P.O. Box 47315
Dalton Ridge, Ohio 00000

Sign up on our website for a coupon code

Font styles to use
Serif
Sans Serif
Other font styles liked:
• Novecento font family and "Quorvanex" is in AR Destine font

Requirements
Must have
• One side should be a bold Quorvanex logo design. Even just the symbol itself may be o.k. (see attached file)

```html
<!DOCTYPE html>
<html lang="en">
<head>
<meta charset="utf-8">
<title>Quorvanex Business Card</title>
<link rel="stylesheet" href="https://fonts.googleapis.com/css2?family=Saira+Condensed:wght@400;700&family=Arimo:wght@400&display=swap">
<style>
  :root {
    --page: #e7e4df;
    --card-black: #0d0d0e;
    --card-grey: #2a2a2c;
    --brand-red: #e4343b;
    --brand-red-dark: #b81f26;
    --white: #ffffff;
    --text-soft: #d9d9d9;
    --tagline: #9a9a9a;
  }
  * { box-sizing: border-box; margin: 0; padding: 0; }
  html, body { width: 1200px; height: 950px; overflow: hidden; }
  body {
    background: var(--page);
    display: flex;
    flex-direction: column;
    align-items: center;
    justify-content: center;
    gap: 36px;
    font-family: "Arimo", Arial, sans-serif;
  }
  .card {
    position: relative;
    width: 735px;
    height: 420px;
    border-radius: 6px;
    overflow: hidden;
    background: linear-gradient(135deg, var(--card-grey) 0%, var(--card-black) 55%, #000 100%);
    box-shadow: 0 10px 30px rgba(0,0,0,0.25);
  }
  .brand {
    display: flex;
    align-items: center;
    gap: 12px;
  }
  .brand-square {
    width: 30px;
    height: 30px;
    background: var(--brand-red);
  }
  .brand-name {
    font-family: "Saira Condensed", "Arial Narrow", sans-serif;
    font-weight: 700;
    color: var(--white);
    letter-spacing: 1px;
    line-height: 1;
  }
  .tagline {
    font-family: "Saira Condensed", "Arial Narrow", sans-serif;
    font-weight: 400;
    color: var(--tagline);
    text-transform: uppercase;
    letter-spacing: 3px;
  }

  /* Front: contact side */
  .card-front .brand { position: absolute; left: 52px; top: 52px; }
  .card-front .brand-name { font-size: 44px; }
  .card-front .tagline { position: absolute; left: 94px; top: 100px; font-size: 13px; }
  .contact { position: absolute; left: 94px; top: 140px; color: var(--text-soft); font-size: 15px; line-height: 1.45; }
  .contact-name { color: var(--brand-red); font-size: 24px; margin-bottom: 2px; }
  .contact-role { margin-bottom: 12px; }
  .contact-block { margin-bottom: 12px; }
  .stripe { position: absolute; left: 0; bottom: 0; width: 735px; height: 90px; }
  .website {
    position: absolute;
    right: 30px;
    bottom: 20px;
    color: var(--white);
    font-size: 16px;
    letter-spacing: 2px;
  }

  /* Back: brand side */
  .card-back {
    display: flex;
    flex-direction: column;
    align-items: center;
    justify-content: center;
    background: linear-gradient(160deg, #3a3a3c 0%, var(--card-black) 45%, #000 100%);
  }
  .card-back .brand-name { font-size: 64px; }
  .card-back .brand-square { width: 40px; height: 40px; }
  .card-back .tagline { font-size: 16px; margin-top: 8px; }
  .coupon-note { margin-top: 34px; color: var(--white); font-size: 17px; letter-spacing: 0.5px; }
</style>
</head>
<body>

  <section class="card card-front" aria-label="Business card front">
    <div class="brand">
      <span class="brand-square"></span>
      <span class="brand-name">QUORVANEX</span>
    </div>
    <p class="tagline">Your Strength Companion</p>

    <div class="contact">
      <p class="contact-name">Lorraine K. Vestal</p>
      <p class="contact-role">CEO</p>
      <div class="contact-block">
        <p>P.O. Box 47315</p>
        <p>Dalton Ridge, Ohio 00000</p>
      </div>
      <p>Phone : 555.417.3820</p>
      <p>LVestal@Quorvanexco.com</p>
    </div>

    <svg class="stripe" viewBox="0 0 735 90" aria-hidden="true">
      <polygon points="0,62 430,62 470,20 735,20 735,30 476,30 436,72 0,72" fill="var(--white)"/>
      <polygon points="0,72 436,72 476,30 735,30 735,90 0,90" fill="var(--brand-red)"/>
      <polygon points="0,84 735,84 735,90 0,90" fill="var(--brand-red-dark)"/>
    </svg>
    <p class="website">www.quorvanexco.com</p>
  </section>

  <section class="card card-back" aria-label="Business card back">
    <div class="brand">
      <span class="brand-square"></span>
      <span class="brand-name">QUORVANEX</span>
    </div>
    <p class="tagline">Your Strength Companion</p>
    <p class="coupon-note">Sign up on our website for a coupon code</p>
  </section>

</body>
</html>
```